Sonic Vale

Rebrand current website and move it to SonicVale.com. Looking for a professional, eye catching, top 10 in World type website. My current website is: https://madebytorven.sitepadhub.com/sonicvale
I would like it moved to sonicvale.com.

```html
<!DOCTYPE html>
<html lang="en">
<head>
<meta charset="utf-8">
<title>Sonic Vale — Music Production</title>
<link href="https://fonts.googleapis.com/css2?family=Montserrat:wght@500;600;700&family=Roboto:wght@400;500;700&display=swap" rel="stylesheet">
<style>
:root{
  --blue:#2ba8e8;
  --blue-dark:#1c8fcc;
  --ink:#050505;
  --panel:#121212;
  --panel-2:#1a1a1a;
  --text:#ffffff;
  --muted:#9a9a9a;
  --grey-head:#bdbdbd;
}
*{box-sizing:border-box;margin:0;padding:0}
html,body{width:1200px;height:5004px;overflow:hidden;background:var(--ink);color:var(--text);font-family:"Roboto",Arial,sans-serif}
.page{position:relative;width:1200px;height:5004px;overflow:hidden}
.abs{position:absolute}
.blue{color:var(--blue)}
.btn{position:absolute;display:flex;align-items:center;justify-content:center;gap:8px;background:var(--blue);color:#fff;border-radius:24px;font:700 14px "Roboto",Arial,sans-serif;text-transform:uppercase}
.btn .arrow{width:14px;height:14px;border-radius:50%;background:#fff;display:inline-flex;align-items:center;justify-content:center}
.btn .arrow::after{content:"";border-left:5px solid var(--blue);border-top:4px solid transparent;border-bottom:4px solid transparent;margin-left:2px}
.section-title{position:absolute;left:0;width:1200px;text-align:center;font:500 42px "Montserrat",Arial,sans-serif;color:var(--grey-head);text-transform:uppercase}
.section-title.white{color:#fff;font-size:36px}

/* header */
.header{position:absolute;left:0;top:0;width:1200px;height:125px;background:#0b0b0b;border-top:3px solid var(--blue)}
.logo{position:absolute;display:flex;align-items:center;gap:10px;font:700 34px "Montserrat",Arial,sans-serif;color:var(--blue)}
.logo .dot{width:14px;height:14px;border-radius:50%;background:var(--blue)}
.contact-chip{position:absolute;display:flex;align-items:center;gap:12px}
.contact-chip .ico{width:38px;height:38px;border-radius:50%;background:#fff;display:flex;align-items:center;justify-content:center}
.contact-chip small{display:block;font-size:11px;color:var(--muted)}
.contact-chip b{display:block;font-size:14px;font-weight:500}
.contact-chip b.big{font-size:20px;font-weight:700}
.nav{position:absolute;left:420px;top:78px;width:780px;height:47px;background:var(--blue);clip-path:polygon(28px 0,100% 0,100% 100%,0 100%)}
.nav ul{list-style:none;display:flex;gap:34px;padding-left:40px;height:100%;align-items:center;font-size:14px;font-weight:500;color:#0b0b0b}

/* hero */
.hero{position:absolute;left:0;top:125px;width:1200px;height:582px}
.hero-photo{position:absolute;inset:0;background:radial-gradient(ellipse at 72% 40%,#6a6a6a 0%,#3a3a3a 30%,#1d1d1d 60%,#0c0c0c 100%)}
.hero h1{position:absolute;left:110px;top:145px;font:700 40px/44px "Montserrat",Arial,sans-serif;text-transform:uppercase}
.hero p{position:absolute;left:110px;top:296px;font-size:16px;line-height:27px;width:420px}

/* about */
.about-band{position:absolute;left:0;top:860px;width:420px;height:425px;background:var(--blue);clip-path:polygon(0 0,110px 105px,110px 343px,340px 343px,420px 425px,0 425px)}
.about-photo{position:absolute;left:122px;top:785px;width:460px;height:410px;background:linear-gradient(160deg,#2c2c2c 0%,#4b5a6b 35%,#7a7d82 60%,#3b3b3b 100%);outline:6px solid #000}
.about-text{position:absolute;left:645px;top:812px;width:440px}
.about-text h3{font:500 20px "Montserrat",Arial,sans-serif;color:var(--grey-head)}
.about-text h2{font:600 44px "Montserrat",Arial,sans-serif;color:var(--blue);margin-top:6px}
.about-text p{font-size:13px;line-height:26px;color:var(--muted);margin-top:18px}

/* latest audio */
.audio-bg{position:absolute;left:0;top:1285px;width:1200px;height:690px;background:linear-gradient(180deg,#0a0a0a 0%,#141414 55%,#0e1a24 100%)}
.track{position:absolute;width:470px;height:140px;background:#121212;border-radius:70px}
.track .art{position:absolute;left:4px;top:4px;width:132px;height:132px;border-radius:50%}
.track .artist{position:absolute;left:168px;top:18px;font-size:14px;color:var(--muted)}
.track .name{position:absolute;left:168px;top:40px;font-size:16px;font-weight:500}
.track .price{position:absolute;left:168px;top:62px;font-size:13px;font-weight:700;color:var(--blue)}
.player{position:absolute;left:158px;top:94px;width:290px;height:26px}
.player span{position:absolute;font-size:9px;color:#ddd}
.player .bar{position:absolute;height:2px;background:#888}
.player .knob{position:absolute;width:8px;height:8px;border:2px solid #fff;border-radius:50%;background:#000}

/* production */
.prod-card{position:absolute;width:470px;height:362px;background:var(--panel-2)}
.prod-card .shot{position:absolute;left:6px;top:6px;width:458px;height:300px}
.prod-card .label{position:absolute;left:0;bottom:0;width:100%;height:56px;display:flex;align-items:center;justify-content:center;font-weight:700;font-size:17px;text-transform:uppercase}
.prod-card.active{background:var(--blue)}
.chev{position:absolute;width:22px;height:22px;border-left:4px solid #ddd;border-bottom:4px solid #ddd}

/* reviews */
.reviews{position:absolute;left:0;top:2655px;width:1200px;height:380px;background:linear-gradient(180deg,#161616,#0d0d0d)}
.quote{position:absolute;left:0;width:1200px;text-align:center}

/* mixing */
.mix h2{position:absolute;left:110px;top:3160px;font:600 32px "Montserrat",Arial,sans-serif;color:var(--grey-head)}
.record-art{position:absolute;left:590px;top:3128px;width:170px;height:334px;background:linear-gradient(90deg,#0a0a0a 0%,#1c1c1c 60%,#241416 100%)}
.mix-photo{position:absolute;left:750px;top:3128px;width:340px;height:334px;background:linear-gradient(135deg,#c2184d 0%,#6a2a8a 40%,#1f4fb0 75%,#0f2c6a 100%)}

/* blog */
.post{position:absolute;top:3718px;width:310px;height:428px;background:var(--panel);border:2px solid #2b2b2b}
.post .thumb{position:absolute;left:0;top:0;width:306px;height:214px}
.post .date{position:absolute;right:0;top:191px;background:var(--blue);font-size:14px;font-weight:500;padding:4px 10px}
.post h4{position:absolute;left:16px;top:232px;width:280px;font-size:16px;line-height:24px;font-weight:500}
.post p{position:absolute;left:16px;top:296px;width:280px;font-size:12.5px;line-height:22px;color:#cfcfcf}
.post .more{position:absolute;left:16px;top:376px;font-size:12.5px;font-weight:700;color:var(--blue)}

/* footer contact */
.info{position:absolute;top:4433px;width:240px;text-align:center}
.info .circle{width:76px;height:76px;margin:0 auto;border-radius:50%;background:var(--blue);display:flex;align-items:center;justify-content:center}
.info h5{font-size:16px;font-weight:700;margin-top:22px}
.info div.v{font-size:14px;margin-top:8px}
.field{position:absolute;height:52px;border:1px solid #262626;border-radius:26px;background:#0a0a0a;font-size:13px;padding:18px 0 0 28px;color:#ddd}
.bottom-bar{position:absolute;left:0;top:4948px;width:1200px;height:56px;background:var(--blue)}
.social{position:absolute;top:4964px;width:32px;height:32px;border:2px solid #fff;border-radius:50%}
</style>
</head>
<body>
<div class="page">

  <header class="header">
    <div class="logo" style="left:110px;top:28px"><span class="dot"></span>SONIC VALE</div>
    <div class="contact-chip" style="left:640px;top:20px">
      <span class="ico"><svg width="20" height="14" viewBox="0 0 20 14"><rect x="1" y="1" width="18" height="12" fill="none" stroke="#2ba8e8" stroke-width="2"/><path d="M1 1l9 7 9-7" fill="none" stroke="#2ba8e8" stroke-width="2"/></svg></span>
      <div><small>Email Us On</small><b>Torven@SonicVale.com</b></div>
    </div>
    <div class="contact-chip" style="left:905px;top:20px">
      <span class="ico"><svg width="18" height="18" viewBox="0 0 24 24"><path d="M6.6 10.8a15 15 0 0 0 6.6 6.6l2.2-2.2a1 1 0 0 1 1-.25 11 11 0 0 0 3.6.6 1 1 0 0 1 1 1V20a1 1 0 0 1-1 1A17 17 0 0 1 3 4a1 1 0 0 1 1-1h3.5a1 1 0 0 1 1 1c0 1.25.2 2.45.6 3.6a1 1 0 0 1-.25 1z" fill="#2ba8e8"/></svg></span>
      <div><small>Call Us Today</small><b class="big">555-013-2240</b></div>
    </div>
    <nav class="nav"><ul><li>Home</li><li>About Me</li><li>Latest Audio</li><li>Shop</li><li>Book Online</li><li>Blog</li><li>Contact Us</li></ul></nav>
  </header>

  <section class="hero">
    <div class="hero-photo" role="img" aria-label="Studio condenser microphone with pop filter above a mixing desk, in black and white"></div>
    <h1>Specializing in<br><span class="blue">All phases of music<br>production</span></h1>
    <p>Intricate but gritty music producer who specializes in all phases of music production.</p>
    <a class="btn" style="left:112px;top:377px;width:238px;height:48px">Contact us today <span class="arrow"></span></a>
  </section>

  <section class="about">
    <div class="about-band"></div>
    <div class="about-photo" role="img" aria-label="Large studio mixing console with monitor speakers"></div>
    <div class="about-text">
      <h3>ABOUT ME</h3>
      <h2>SONIC VALE</h2>
      <p>CEO of Sonic Vale, Torven Ashdale has always pushed himself to achieve success in the music industry. Using his advanced technical abilities and own unique style, Sonic Vale has surpassed many companies to become one of the premier music production organizations globally. Get in touch to learn more about his background, experience and latest projects.</p>
    </div>
    <a class="btn" style="left:645px;top:1115px;width:180px;height:44px;font-size:13px">Learn more <span class="arrow"></span></a>
  </section>

  <section class="latest-audio">
    <div class="audio-bg" role="img" aria-label="Dim studio room with speakers behind the track list"></div>
    <h2 class="section-title" style="top:1362px">Latest <span class="blue">Audio</span></h2>

    <div class="track" style="left:112px;top:1465px">
      <div class="art" role="img" aria-label="Vintage microphone cover art" style="background:radial-gradient(circle,#9a9a9a,#3a3a3a)"></div>
      <div class="artist">Torven</div><div class="name">NIGHT DRIVE (Remastered)</div><div class="price">Single $200.00</div>
      <div class="player"><span style="left:6px;top:6px">▶ ■</span><span style="left:36px;top:0">Sound.mp3</span><span style="left:125px;top:0">00:00/02:06</span><div class="bar" style="left:36px;top:14px;width:150px"></div><div class="knob" style="left:34px;top:10px"></div><span style="left:196px;top:6px">◀</span><div class="bar" style="left:208px;top:14px;width:48px;background:var(--blue)"></div><div class="knob" style="left:252px;top:10px"></div><span style="left:266px;top:6px">⇆</span></div>
    </div>
    <div class="track" style="left:620px;top:1465px">
      <div class="art" role="img" aria-label="Audio software on a screen cover art" style="background:radial-gradient(circle,#8fa8c8,#1e2d44)"></div>
      <div class="artist">Torven</div><div class="name">NIGHT DRIVE (Remastered)</div><div class="price">Single $200.00</div>
      <div class="player"><span style="left:6px;top:6px">▶ ■</span><span style="left:36px;top:0">Sound.mp3</span><span style="left:125px;top:0">00:00/02:06</span><div class="bar" style="left:36px;top:14px;width:150px"></div><div class="knob" style="left:34px;top:10px"></div><span style="left:196px;top:6px">◀</span><div class="bar" style="left:208px;top:14px;width:48px;background:var(--blue)"></div><div class="knob" style="left:252px;top:10px"></div><span style="left:266px;top:6px">⇆</span></div>
    </div>
    <div class="track" style="left:112px;top:1653px">
      <div class="art" role="img" aria-label="Studio gear under a lamp cover art" style="background:radial-gradient(circle,#c9b48a,#2a2418)"></div>
      <div class="artist">Torven</div><div class="name">NIGHT DRIVE (Remastered)</div><div class="price">Single $200.00</div>
      <div class="player"><span style="left:6px;top:6px">▶ ■</span><span style="left:36px;top:0">Sound.mp3</span><span style="left:125px;top:0">00:00/02:06</span><div class="bar" style="left:36px;top:14px;width:150px"></div><div class="knob" style="left:34px;top:10px"></div><span style="left:196px;top:6px">◀</span><div class="bar" style="left:208px;top:14px;width:48px;background:var(--blue)"></div><div class="knob" style="left:252px;top:10px"></div><span style="left:266px;top:6px">⇆</span></div>
    </div>
    <div class="track" style="left:620px;top:1653px">
      <div class="art" role="img" aria-label="Warm-lit recording desk cover art" style="background:radial-gradient(circle,#d68a4a,#3a1e10)"></div>
      <div class="artist">Torven</div><div class="name">NIGHT DRIVE (Remastered)</div><div class="price">Single $200.00</div>
      <div class="player"><span style="left:6px;top:6px">▶ ■</span><span style="left:36px;top:0">Sound.mp3</span><span style="left:125px;top:0">00:00/02:06</span><div class="bar" style="left:36px;top:14px;width:150px"></div><div class="knob" style="left:34px;top:10px"></div><span style="left:196px;top:6px">◀</span><div class="bar" style="left:208px;top:14px;width:48px;background:var(--blue)"></div><div class="knob" style="left:252px;top:10px"></div><span style="left:266px;top:6px">⇆</span></div>
    </div>
    <a class="btn" style="left:513px;top:1851px;width:174px;height:44px;font-size:13px">Learn more <span class="arrow"></span></a>
  </section>

  <section class="production">
    <h2 class="section-title" style="top:2070px">Our Music <span class="blue">Production</span></h2>
    <div class="chev" style="left:50px;top:2338px;transform:rotate(45deg)"></div>
    <div class="chev" style="left:1130px;top:2338px;transform:rotate(-135deg)"></div>
    <div class="prod-card" style="left:110px;top:2168px">
      <div class="shot" role="img" aria-label="Film crew working on a movie set under studio lights" style="background:linear-gradient(180deg,#3a3a3a 0%,#8a7a5e 45%,#2a241c 100%)"></div>
      <div class="label">Movies</div>
    </div>
    <div class="prod-card active" style="left:620px;top:2168px">
      <div class="shot" role="img" aria-label="Crew shooting a commercial on a lit set" style="background:linear-gradient(180deg,#2e3440 0%,#9a8a6a 45%,#2a2620 100%)"></div>
      <div class="label">Commercials</div>
    </div>
  </section>

  <section class="reviews-wrap">
    <div class="reviews" role="img" aria-label="Dark close-up of mixing desk faders"></div>
    <h2 class="section-title white" style="top:2722px">Client <span class="blue">Reviews</span></h2>
    <div class="quote" style="top:2805px;font:700 64px/1 Georgia,serif;color:var(--blue)">“</div>
    <p class="quote" style="top:2858px;font-size:20px;line-height:31px;font-weight:700">Music expresses that which cannot be said and on which it is<br>impossible to be silent</p>
    <p class="quote" style="top:2940px;font-size:14px;color:var(--blue)">Marcel Devaux</p>
  </section>

  <section class="mix">
    <h2>MIXING AND <span class="blue">MASTERING</span></h2>
    <p class="abs" style="left:110px;top:3207px;font-size:12px;color:#bbb">SKU: 364215376135191</p>
    <p class="abs" style="left:110px;top:3255px;font-size:19px;font-weight:700;color:var(--blue)">$150.00</p>
    <p class="abs" style="left:110px;top:3288px;width:370px;font-size:14px;line-height:25px">Get your music mix and mastered professionally to industry standards.</p>
    <a class="btn" style="left:110px;top:3370px;width:180px;height:46px;font-size:13px">Shop now <span class="arrow"></span></a>
    <div class="record-art" role="img" aria-label="Vinyl record partly tucked behind the product photo"></div>
    <div class="mix-photo" role="img" aria-label="Vocalist in headphones singing into a studio microphone under red and blue light"></div>
  </section>

  <section class="blog">
    <h2 class="section-title white" style="top:3632px;font-size:34px">Latest <span class="blue">Blog</span></h2>
    <article class="post" style="left:110px">
      <div class="thumb" role="img" aria-label="Guitarist recording next to a laptop" style="background:linear-gradient(135deg,#d8d2c8,#8a3a2a 50%,#1e1e1e)"></div>
      <span class="date">Jan 23, 2020</span>
      <h4>5 Things the Artist Needs to Know Before Recording</h4>
      <p>This is your blog post. Blogs are a great way to connect with your audience and keep them coming back.</p>
      <span class="more">READ MORE »</span>
    </article>
    <article class="post" style="left:444px">
      <div class="thumb" role="img" aria-label="Headphones resting on studio equipment" style="background:linear-gradient(135deg,#2a3a3a,#4e6a6a 50%,#141414)"></div>
      <span class="date">Jan 23, 2020</span>
      <h4>Recording Equipment Must-Haves for Every Studio</h4>
      <p>This is your blog post. Great looking images make your blog posts more visually compelling for your audience,</p>
      <span class="more">READ MORE »</span>
    </article>
    <article class="post" style="left:778px">
      <div class="thumb" role="img" aria-label="Band rehearsing in a rehearsal room" style="background:linear-gradient(135deg,#c8b48a,#6a4a2a 50%,#1e1a14)"></div>
      <span class="date">Jan 23, 2020</span>
      <h4>Sound Check: Recording Tips from the Pros</h4>
      <p>This is your blog post. To really engage your site visitors we suggest you blog about subjects that are related</p>
      <span class="more">READ MORE »</span>
    </article>
  </section>

  <footer class="contact">
    <div class="logo" style="left:0;width:1200px;justify-content:center;top:4325px"><span class="dot"></span>SONIC VALE</div>
    <div class="info" style="left:140px">
      <div class="circle"><svg width="30" height="30" viewBox="0 0 24 24"><path d="M6.6 10.8a15 15 0 0 0 6.6 6.6l2.2-2.2a1 1 0 0 1 1-.25 11 11 0 0 0 3.6.6 1 1 0 0 1 1 1V20a1 1 0 0 1-1 1A17 17 0 0 1 3 4a1 1 0 0 1 1-1h3.5a1 1 0 0 1 1 1c0 1.250.2 2.45.6 3.6a1 1 0 0 1-.25 1z" fill="#fff"/></svg></div>
      <h5>PHONE</h5><div class="v">555-013-2240</div>
    </div>
    <div class="info" style="left:452px">
      <div class="circle"><svg width="30" height="22" viewBox="0 0 20 14"><rect x="0" y="0" width="20" height="14" rx="1" fill="#fff"/><path d="M1 1l9 7 9-7" fill="none" stroke="#2ba8e8" stroke-width="1.6"/></svg></div>
      <h5>Email</h5><div class="v">Torven@SonicVale.com</div>
    </div>
    <div class="info" style="left:808px">
      <div class="circle"><svg width="24" height="30" viewBox="0 0 24 30"><path d="M12 0a11 11 0 0 0-11 11c0 8 11 19 11 19s11-11 11-19A11 11 0 0 0 12 0z" fill="#fff"/><circle cx="12" cy="11" r="4" fill="#2ba8e8"/></svg></div>
      <h5>Address</h5>
      <div class="v" style="width:130px;margin:8px auto 0;background:#fff;color:var(--blue);border-radius:16px;padding:7px 0;font-size:12px;font-weight:500">Marlow, GA</div>
    </div>

    <div class="field" style="left:195px;top:4612px;width:392px">Name</div>
    <div class="field" style="left:195px;top:4678px;width:392px">Email Address</div>
    <div class="field" style="left:195px;top:4743px;width:392px">Phone Number</div>
    <div class="field" style="left:610px;top:4612px;width:395px;height:183px;border-radius:26px">Message</div>
    <a class="btn" style="left:500px;top:4846px;width:206px;height:50px;font-size:15px">Submit now <span class="arrow"></span></a>

    <div class="bottom-bar"></div>
    <p class="abs" style="left:110px;top:4968px;font-size:14px;font-weight:500">Sonic Vale. Copyright 2021. ALL RIGHTS RESERVED.</p>
    <span class="social" style="left:970px"></span>
    <span class="social" style="left:1012px"></span>
    <span class="social" style="left:1054px"></span>
  </footer>

</div>
</body>
</html>
```